Personal Injury Law Firm needs folder design

Need a folder design for our personal injury law firm, Corrow & Talmidge, LLC. to give to all of our clients with their documents at the end of their case. I've attached our branding guide. We are branded as the 5 star law firm that fights for our clients like family. It should incorporate our colors or Green and White. We'd like to convey a message of moving on to the next chapter after finishing their case.

```html
<!DOCTYPE html>
<html lang="en">
<head>
<meta charset="utf-8">
<title>Corrow &amp; Talmidge, LLC — Client Folder</title>
<link rel="stylesheet" href="https://fonts.googleapis.com/css2?family=Cinzel:wght@600&family=Open+Sans:wght@400;600&family=Lato:wght@400;700&display=swap">
<style>
  :root {
    --green: #16a67b;
    --deep: #0b3338;
    --paper: #ffffff;
    --inner: #f1f1f1;
    --stage: #b8b7b8;
    --ink: #222222;
    --muted: #555555;
  }
  * { box-sizing: border-box; margin: 0; padding: 0; }
  html, body { width: 982px; height: 1200px; overflow: hidden; background: var(--stage); }
  .canvas { position: relative; width: 982px; height: 1200px; }

  .spread {
    position: absolute; left: 71px; width: 840px; height: 560px;
    display: flex; box-shadow: 0 8px 24px rgba(0,0,0,.25);
  }
  .spread--outer { top: 30px; }
  .spread--inner { top: 620px; }
  .panel { position: relative; width: 420px; height: 560px; overflow: hidden; background: var(--paper); }
  .panel + .panel { border-left: 1px solid #e2e2e2; }

  /* back cover */
  .brand { position: absolute; left: 46px; top: 238px; display: flex; align-items: center; gap: 12px; }
  .brand__square { width: 62px; height: 58px; background: var(--green); flex: none; }
  .brand__name { font-family: "Cinzel", serif; font-weight: 600; font-size: 19px; color: var(--green); letter-spacing: .5px; white-space: nowrap; }
  .brand__tag { font-family: "Cinzel", serif; font-weight: 600; font-size: 7.5px; letter-spacing: 3px; color: var(--deep); margin-top: 4px; text-align: center; border-top: 1px solid var(--deep); padding-top: 4px; }

  .contact { position: absolute; left: 24px; bottom: 28px; font-family: "Open Sans", sans-serif; font-size: 12px; color: var(--ink); line-height: 1.5; }
  .contact__row { display: flex; align-items: center; gap: 6px; }
  .contact__row svg { width: 10px; height: 10px; flex: none; }
  .address { position: absolute; right: 22px; bottom: 60px; font-family: "Open Sans", sans-serif; font-size: 12px; color: var(--ink); text-align: right; line-height: 1.45; }

  /* front cover */
  .cover-square { position: absolute; left: 56px; top: 92px; width: 304px; height: 290px; background: var(--green); }
  .cover-wave { position: absolute; left: 0; bottom: 0; width: 420px; height: 120px; }

  /* inner spread */
  .panel--inside { background: linear-gradient(90deg, #ffffff 0%, var(--inner) 60%, #d9d9d9 100%); }
  .panel--inside-right { background: linear-gradient(90deg, #e4e4e4 0%, var(--inner) 25%, #ffffff 100%); }
  .pocket { position: absolute; left: 0; bottom: 0; width: 420px; height: 200px; }

  .letter {
    position: absolute; left: 34px; top: 24px; width: 340px; height: 480px;
    background: var(--paper); box-shadow: 0 2px 10px rgba(0,0,0,.18);
    padding: 22px 24px; font-family: "Lato", sans-serif; color: var(--ink);
  }
  .letter__head { display: flex; justify-content: space-between; align-items: flex-start; }
  .letter .brand { position: static; gap: 6px; margin-top: 22px; }
  .letter .brand__square { width: 26px; height: 24px; }
  .letter .brand__name { font-size: 9.5px; }
  .letter .brand__tag { font-size: 4.5px; letter-spacing: 1.6px; margin-top: 2px; padding-top: 2px; }
  .letter__contact { border-left: 1px solid var(--green); padding-left: 7px; font-size: 6px; line-height: 1.45; color: var(--muted); }
  .letter__date { margin-top: 38px; font-size: 7px; }
  .letter__recipient { margin-top: 10px; font-size: 6.5px; line-height: 1.35; }
  .letter__recipient + .letter__recipient { margin-top: 8px; }
  .letter__salutation { margin-top: 10px; font-size: 8px; font-weight: 700; }
  .letter__body p { margin-top: 8px; font-size: 6.2px; line-height: 1.3; }
</style>
</head>
<body>
<div class="canvas">

  <!-- outer spread: back cover and front cover -->
  <section class="spread spread--outer">
    <div class="panel panel--back">
      <div class="brand">
        <div class="brand__square"></div>
        <div>
          <div class="brand__name">CORROW &amp; TALMIDGE, LLC</div>
          <div class="brand__tag">ATTORNEYS AT LAW</div>
        </div>
      </div>

      <div class="contact">
        <div class="contact__row">
          <svg viewBox="0 0 10 10"><circle cx="5" cy="5" r="5" fill="var(--green)"/><path d="M3 2.6l1 .9-.5.8c.4.8 1 1.4 1.8 1.8l.8-.5.9 1-.7.8C4.6 7.2 2.8 5.4 2.4 3.3z" fill="#fff"/></svg>
          <span>(555) 410-2286</span>
        </div>
        <div class="contact__row">
          <svg viewBox="0 0 10 10"><circle cx="5" cy="5" r="5" fill="var(--green)"/><rect x="2.4" y="3.2" width="5.2" height="3.6" fill="none" stroke="#fff" stroke-width=".7"/><path d="M2.4 3.2L5 5.2l2.6-2" fill="none" stroke="#fff" stroke-width=".7"/></svg>
          <span>office@corrowtalmidge.com</span>
        </div>
        <div class="contact__row">
          <svg viewBox="0 0 10 10"><circle cx="5" cy="5" r="5" fill="var(--green)"/><circle cx="5" cy="5" r="2.8" fill="none" stroke="#fff" stroke-width=".6"/><path d="M2.2 5h5.6M5 2.2v5.6" stroke="#fff" stroke-width=".6"/></svg>
          <span>www.corrowtalmidge.com</span>
        </div>
      </div>

      <div class="address">
        4120 Harbor Crest Drive<br>Port Alder, FL 33900
      </div>
    </div>

    <div class="panel panel--front">
      <div class="cover-square"></div>
      <svg class="cover-wave" viewBox="0 0 420 120" preserveAspectRatio="none" aria-hidden="true">
        <path d="M0 40 C60 80 120 95 190 70 C260 45 330 25 420 22 L420 120 L0 120 Z" fill="var(--deep)"/>
        <path d="M0 28 C60 68 120 82 190 58 C260 34 330 14 420 12" fill="none" stroke="var(--green)" stroke-width="5"/>
      </svg>
    </div>
  </section>

  <!-- inner spread: pockets with letterhead -->
  <section class="spread spread--inner">
    <div class="panel panel--inside">
      <svg class="pocket" viewBox="0 0 420 200" preserveAspectRatio="none" aria-hidden="true">
        <path d="M0 60 L330 8 C350 5 365 12 372 24 L420 100 L420 200 L0 200 Z" fill="var(--green)"/>
      </svg>
    </div>

    <div class="panel panel--inside-right">
      <article class="letter">
        <div class="letter__head">
          <div class="brand">
            <div class="brand__square"></div>
            <div>
              <div class="brand__name">CORROW &amp; TALMIDGE, LLC</div>
              <div class="brand__tag">ATTORNEYS AT LAW</div>
            </div>
          </div>
          <div class="letter__contact">
            Your address, City<br>State, Zip 1234<br>123 456 789<br>info@yourgmail.com<br>www.yourwebsite.com
          </div>
        </div>

        <div class="letter__date">January-03-2020</div>
        <div class="letter__recipient">Mr. John Doe<br>President</div>
        <div class="letter__recipient">Link Corpporation<br>123 Street Name, Suite# 10<br>City, State, 120023</div>
        <div class="letter__salutation">Dear Mr, John</div>
        <div class="letter__body">
          <p>Lorem ipsum dolor sit amet, consectetur adipiscing elit, sed do eiusmod tempor incididunt ut labore et dolore magna aliqua. Ut enim ad minim veniam, quis nostrud exercitation ullamco laboris nisi ut aliquip ex ea commodo consequat. Duis aute irure dolor in reprehenderit in voluptate velit esse cillum dolore eu fugiat nulla pariatur.</p>
          <p>Lorem ipsum dolor sit amet, consectetur adipiscing elit, sed do eiusmod tempor incididunt ut labore et dolore magna aliqua. Ut enim ad minim veniam, quis nostrud exercitation ullamco laboris nisi ut aliquip ex ea commodo consequat. Duis aute irure dolor in reprehenderit in voluptate velit esse cillum dolore eu fugiat nulla pariatur.</p>
          <p>Lorem ipsum dolor sit amet, consectetur adipiscing elit, sed do eiusmod tempor incididunt ut labore et dolore magna aliqua. Ut enim ad minim veniam, quis nostrud exercitation ullamco laboris nisi ut aliquip ex ea commodo consequat.</p>
          <p>Excepteur sint occaecat cupidatat non proident, sunt in culpa qui officia deserunt mollit anim id est laborum. re et dolore magnam aliquam quaerat voluptatem.</p>
          <p>Regards</p>
        </div>
      </article>

      <svg class="pocket" viewBox="0 0 420 200" preserveAspectRatio="none" aria-hidden="true">
        <path d="M0 200 L12 60 C14 44 26 34 44 32 L400 4 L420 60 L420 200 Z" fill="var(--green)"/>
      </svg>
    </div>
  </section>

</div>
</body>
</html>
```